Corvane Automotive Reconditioning Business Card

We need a professional business card that features our logo, a picture of the employee, and a brief list of our services.
I've attached a logo, and will attach photos at a later date.
The four services that need to be listed are Bumper repair and repainting, road rash repair, clear coat scratch repair, and automotive touch-up.
Target Market(s)
30 - 40 year male general managers of automobile dealerships. They are used to seeing every vendor gimmick under the sun. This brochure needs to impress with its simplicity and honesty.
Industry/Entity Type
Automotive
Look and feel

```html
<!DOCTYPE html>
<html lang="en">
<head>
<meta charset="utf-8">
<title>Corvane Automotive Reconditioning – Business Card</title>
<link href="https://fonts.googleapis.com/css2?family=Open+Sans:wght@300;400;600;800&display=swap" rel="stylesheet">
<style>
  :root {
    --bg: #e4e2df;
    --card: #3a3a3c;
    --card-edge: #2c2c2e;
    --panel: #ffffff;
    --ink: #2b2b2b;
    --ink-soft: #444444;
    --accent: #f0561d;
    --name: #e9e9e9;
    --photo-a: #efe9e4;
    --photo-b: #8a6f60;
  }
  * { box-sizing: border-box; margin: 0; padding: 0; }
  html, body { width: 1200px; height: 900px; overflow: hidden; }
  body {
    background: var(--bg);
    font-family: "Open Sans", Arial, sans-serif;
    position: relative;
  }
  .card {
    position: absolute;
    left: 250px;
    width: 700px;
    height: 400px;
    background: var(--card);
    border-radius: 26px;
    box-shadow: 0 0 0 1px var(--card-edge), 0 10px 24px rgba(0,0,0,.18);
  }
  .card--back { top: 30px; }
  .card--front { top: 470px; }

  .panel {
    position: absolute;
    background: var(--panel);
    border-radius: 22px;
  }

  /* back */
  .card--back .panel { left: 26px; top: 26px; right: 26px; bottom: 26px; }
  .brand {
    display: flex;
    align-items: center;
    gap: 10px;
    color: var(--ink);
    font-weight: 800;
    text-transform: uppercase;
    line-height: 1.05;
  }
  .brand__dot {
    flex: none;
    width: 16px; height: 16px;
    border-radius: 50%;
    background: var(--accent);
  }
  .card--back .brand {
    position: absolute;
    left: 40px; top: 130px;
    width: 300px;
    font-size: 24px;
  }
  .services {
    position: absolute;
    left: 395px; top: 120px;
    list-style: none;
    font-size: 15px;
    color: var(--ink);
    line-height: 1.55;
  }

  /* front */
  .photo-panel {
    left: 26px; top: 26px;
    width: 270px; height: 290px;
    overflow: hidden;
  }
  .photo {
    position: absolute;
    left: 0; top: 0; width: 100%; height: 100%;
    background: radial-gradient(ellipse at 50% 45%, var(--photo-b) 0 32%, var(--photo-a) 70%);
  }
  .person-name {
    position: absolute;
    left: 26px; top: 332px;
    width: 270px;
    text-align: center;
    color: var(--name);
    font-weight: 300;
    font-size: 22px;
    letter-spacing: 3px;
  }
  .info-panel { left: 312px; top: 26px; right: 26px; bottom: 26px; }
  .card--front .brand {
    position: absolute;
    left: 30px; top: 34px;
    width: 300px;
    font-size: 20px;
  }
  .address {
    position: absolute;
    left: 30px; top: 128px;
    font-size: 15px;
    color: var(--ink-soft);
    line-height: 1.45;
  }
  .contacts {
    position: absolute;
    left: 30px; top: 196px;
    list-style: none;
    font-size: 15px;
    color: var(--ink-soft);
  }
  .contacts li {
    display: flex;
    align-items: center;
    gap: 10px;
    height: 26px;
  }
  .contacts svg { width: 15px; height: 15px; flex: none; }
</style>
</head>
<body>

<section class="card card--back" aria-label="Business card back">
  <div class="panel">
    <div class="brand"><span class="brand__dot"></span><span>Corvane Automotive Reconditioning</span></div>
    <ul class="services">
      <li>Bumper repair and repainting</li>
      <li>Road rash repair</li>
      <li>Clear coat scratch repair</li>
      <li>Automotive touch-up</li>
    </ul>
  </div>
</section>

<section class="card card--front" aria-label="Business card front">
  <div class="panel photo-panel">
    <div class="photo" role="img" aria-label="Employee portrait photo"></div>
  </div>
  <p class="person-name">DANIEL HARROW</p>

  <div class="panel info-panel">
    <div class="brand"><span class="brand__dot"></span><span>Corvane Automotive Reconditioning</span></div>
    <p class="address">4820 N. Saguaro Ln.<br>Mesa, AZ 85201</p>
    <ul class="contacts">
      <li>
        <svg viewBox="0 0 16 16" aria-hidden="true"><path fill="#f0561d" d="M2 5c0-2 2-3 6-3s6 1 6 3v1h-3V5H5v1H2zM4 7h8l2 7H2z"/><circle cx="8" cy="10.5" r="2" fill="#fff"/></svg>
        <span>555-214-0370</span>
      </li>
      <li>
        <svg viewBox="0 0 16 16" aria-hidden="true"><rect x="4" y="1" width="8" height="14" rx="1.5" fill="#f0561d"/><rect x="5.5" y="3" width="5" height="7" fill="#fff"/></svg>
        <span>555-214-0380</span>
      </li>
      <li>
        <svg viewBox="0 0 16 16" aria-hidden="true"><rect x="1" y="3" width="14" height="10" fill="none" stroke="#f0561d" stroke-width="1.6"/><path d="M1 3l7 6 7-6" fill="none" stroke="#f0561d" stroke-width="1.6"/></svg>
        <span>info@corvaneauto.com</span>
      </li>
      <li>
        <svg viewBox="0 0 16 16" aria-hidden="true"><g fill="none" stroke="#f0561d" stroke-width="1.4"><circle cx="8" cy="8" r="6.5"/><ellipse cx="8" cy="8" rx="3" ry="6.5"/><path d="M1.5 8h13M2.5 4.5h11M2.5 11.5h11"/></g></svg>
        <span>www.corvaneauto.com</span>
      </li>
    </ul>
  </div>
</section>

</body>
</html>
```